We need UI/UX design for a public, informational website for The Copper Lantern.
The pages, structure, and content scope are already defined. Designers are required to work only on the UI/UX layout of these existing pages, focusing on clarity, hierarchy, spacing, and usability. Do not add, remove, rename, or reinterpret pages or content.
The website is strictly informational only. It must not include accounts, onboarding, payments, custody, escrow administration, marketplaces, dashboards, or any transactional functionality.
Scope of work
Apply UI/UX design to the predefined website pages
Design layout for text, images, notices, and sections
Ensure consistent components and layout patterns across page types
Optimize layouts for long form, compliance focused content
Content writing, page creation, and branding changes are out of scope.
Structure reference
The complete page list, hierarchy, and content definitions are provided in the technical documentation and must be treated as the primary source of truth.
A Figma link is provided only as a light visual reference for page existence and structure:
https://meadow-knot-48203956.plumsite.example/
Designers must rely on the documentation for in depth and authoritative reference.
Brand guidelines
The Copper Lantern has existing brand guidelines and official logos, including light and dark versions. These assets will be provided and must be followed exactly. Designers must not redesign, alter, or reinterpret the brand identity.
Look and feel direction
The desired visual direction is inspired by:
https://ledgerwaltz.example/
This reference is provided only to indicate:
Institutional and enterprise tone
Clean, modern typography
Strong hierarchy and generous whitespace
Editorial, content first layouts
Do not copy branding, layouts, components, or assets from the reference site.
Hero section direction
The hero section should follow a similar structural approach to the hero used on https://ledgerwaltz.example/
, meaning:
Strong editorial framing
Clear headline hierarchy
Calm, institutional first impression
However, the background video must be Abu Dhabi focused, not generic or global. The video should visually reflect:
Abu Dhabi skyline or architectural language
Institutional, sovereign, long term infrastructure tone
Clean, slow, cinematic motion
No promotional, marketing, or lifestyle visuals
The hero must remain informational, restrained, and credible. No hype. No calls to invest. No implied participation.
Constraints
One global primary CTA only: “Continue to Halvemark” (external)
All other interactions must be informational
No visuals or language implying offers, investment, eligibility, or participation
Clear separation between informational content and any external operational platforms
Deliverables
High fidelity UI/UX designs created in Figma, covering:
Desktop layouts
Tablet layouts where relevant
Mobile layouts
Complete Figma file(s) including:
All designed pages defined in the technical documentation
A reusable component library (headers, footers, cards, notice panels, forms, CTAs, typography styles, spacing system)
Clearly defined layout grids, spacing rules, and text styles
Proper use of components and variants, not detached frames
Designs prepared for developer handoff, including:
Clear layer naming and structure
Auto layout where appropriate
Consistent use of styles and components
Responsive behavior demonstrated within Figma
Notes or annotations only where necessary for clarity
No prototypes, interactions, or motion design beyond basic layout states, unless explicitly requested. The focus is static UI/UX clarity, not animation.
A detailed technical specification document and official brand assets will be provided.
Any designs delivered outside Figma, that alter structure or content, or that ignore the defined constraints, boundaries, or tone will be rejected.

```html
<!DOCTYPE html>
<html lang="en">
<head>
<meta charset="utf-8">
<title>The Copper Lantern</title>
<link href="https://fonts.googleapis.com/css2?family=Outfit:wght@700;800&family=Albert+Sans:wght@400;500;600&display=swap" rel="stylesheet">
<style>
:root{
  --navy:#0b1a33;
  --ink:#1d2433;
  --violet:#a88cf7;
  --mist:#f1f2f4;
  --white:#ffffff;
  --line:#0b1a33;
}
*{box-sizing:border-box;margin:0;padding:0}
html,body{width:1200px;height:3852px;overflow:hidden}
body{position:relative;background:var(--white);font-family:"Albert Sans",sans-serif;color:var(--ink);font-size:16px}
.abs{position:absolute}
h1,h2,h3,.heading{font-family:"Outfit",sans-serif;font-weight:800;color:var(--navy);letter-spacing:-0.02em}
.rule{position:absolute;width:40px;height:3px;background:var(--line)}
.copy{line-height:34.4px;font-size:16px;color:var(--ink)}
.justify{text-align:justify}
.btn{position:absolute;display:flex;align-items:center;justify-content:center;border-radius:24px;font-size:14px;font-weight:500;text-transform:uppercase;letter-spacing:0.02em;text-decoration:none}
.btn-dark{background:var(--navy);color:var(--white)}
.btn-violet{background:var(--violet);color:var(--white)}
.btn-outline{border:1.5px solid var(--navy);color:var(--navy);background:var(--white);font-size:13px}

/* hero */
.hero{position:absolute;left:0;top:0;width:1200px;height:512px;border-radius:0 0 70px 70px;overflow:hidden}
.hero-media{position:absolute;inset:0;background:
  linear-gradient(180deg,rgba(255,255,255,0) 60%,rgba(120,140,150,.55) 100%),
  linear-gradient(90deg,#eef2f6 0%,#e6ecf1 40%,#b9c8d3 62%,#7f98a9 78%,#5d7688 100%)}
.brand{position:absolute;display:flex;align-items:center;gap:10px;font-family:"Albert Sans",sans-serif;font-weight:500;font-size:17px;color:var(--navy);text-transform:uppercase;letter-spacing:0.03em}
.brand-dot{width:14px;height:14px;border-radius:50%;background:var(--violet)}
.nav{position:absolute;left:450px;top:45px;width:638px;display:flex;justify-content:space-between;font-size:13px;font-weight:500;text-transform:uppercase;color:var(--navy)}
.nav .active{color:var(--violet)}
.hero h1{position:absolute;left:112px;top:143px;font-size:33px}
.hero .copy{position:absolute;left:112px;top:200px;width:460px;line-height:34.4px}

/* media shapes */
.photo{position:absolute}
.photo-skyline{left:112px;top:601px;width:471px;height:476px;border-radius:0 238px 238px 238px;background:linear-gradient(160deg,#c9d3da 0%,#8ea3b2 40%,#5f7b8d 65%,#3f6a78 100%)}
.photo-network{left:652px;top:2002px;width:428px;height:430px;border-radius:215px 0 215px 215px;background:radial-gradient(circle at 55% 45%,#b9c6d2 0%,#a3b3c2 70%,#97a8b8 100%)}
.photo-stones{left:112px;top:2522px;width:428px;height:430px;border-radius:0 215px 215px 215px;background:radial-gradient(circle at 50% 55%,#8d8578 0%,#6e6a5c 45%,#7a6a3e 75%,#5f5a40 100%)}

/* sections */
.band{position:absolute;left:0;width:1200px;background:var(--mist);border-radius:70px 70px 0 0}
.center{position:absolute;left:0;width:1200px;text-align:center}
.card{position:absolute;top:1397px;width:295px;height:355px;background:var(--white);border-radius:6px}
.card-num{position:absolute;left:0;top:21px;width:81px;height:59px;background:var(--navy);border-radius:0 30px 30px 0;color:var(--white);font-family:"Outfit",sans-serif;font-weight:800;font-size:33px;display:flex;align-items:center;padding-left:20px}
.card h3{position:absolute;left:21px;top:110px;font-size:18px;letter-spacing:0}
.card .copy{position:absolute;left:21px;top:148px;width:256px}
.card .btn{left:21px;top:280px;width:126px;height:42px}

/* footer */
.footer{position:absolute;left:0;top:3460px;width:1200px;height:392px;background:var(--navy);color:var(--white)}
.footer .brand{color:var(--white)}
.footer h4{position:absolute;top:62px;font-family:"Outfit",sans-serif;font-weight:700;font-size:20px;color:var(--white)}
.footer ul{position:absolute;top:110px;list-style:none;font-size:15px;line-height:34.4px}
.footer .legal{position:absolute;left:118px;top:259px;font-size:15px;line-height:29px}
</style>
</head>
<body>

<header class="hero">
  <div class="hero-media" role="img" aria-label="Abu Dhabi skyline with towers along the waterfront under a pale sky"></div>
  <div class="brand" style="left:112px;top:54px"><span class="brand-dot"></span>The Copper Lantern</div>
  <nav class="nav">
    <span class="active">Home</span><span>Framework</span><span>Projects</span><span>Halvemark</span><span>Insights</span><span>Company</span><span>Contact</span>
  </nav>
  <h1>The Copper Lantern</h1>
  <p class="copy">The Copper Lantern is a governance and project origination group. Its purpose is to define structural standards and oversight principles for complex initiatives.</p>
  <a class="btn btn-dark" style="left:112px;top:332px;width:225px;height:45px">Continue to Halvemark</a>
  <a class="btn btn-violet" style="left:360px;top:332px;width:225px;height:45px">Learn the Framework</a>
</header>

<section class="governance">
  <div class="photo photo-skyline" role="img" aria-label="Abu Dhabi skyline towers beside the water"></div>
  <h2 class="abs" style="left:657px;top:586px;font-size:33px;line-height:47px;width:440px">Governance and Project Origination</h2>
  <div class="rule" style="left:657px;top:703px"></div>
  <p class="abs copy justify" style="left:657px;top:733px;width:431px">Governance in this context refers to the standards that determine how projects are structured and how oversight is described. Origination refers to the initial design and definition of an initiative, including role separation, reporting expectations, and boundary setting before execution begins. The Copper Lantern focuses on these governance-level elements rather than on operating day-to-day workflows.</p>
  <a class="btn btn-dark" style="left:658px;top:1038px;width:147px;height:45px">Learn More</a>
</section>

<section class="band" style="top:1170px;height:745px"></section>
<section class="ecosystem">
  <h2 class="center" style="top:1220px;font-size:31px">How the Ecosystem Works</h2>
  <div class="rule" style="left:580px;top:1281px"></div>
  <p class="center" style="top:1322px;font-size:16px">At a high level, the ecosystem can be understood as three layers:</p>

  <article class="card" style="left:112px">
    <div class="card-num">01</div>
    <h3>Governance</h3>
    <p class="copy">defines standards, explains role boundaries, and publishes framework information</p>
    <a class="btn btn-outline">Read More</a>
  </article>
  <article class="card" style="left:453px">
    <div class="card-num">02</div>
    <h3>Operations</h3>
    <p class="copy">manages workflow processes such as documentation steps and record-anchored audit</p>
    <a class="btn btn-outline">Read More</a>
  </article>
  <article class="card" style="left:793px">
    <div class="card-num">03</div>
    <h3>Project Execution</h3>
    <p class="copy">occurs at the project level through dedicated structures that hold responsibilities</p>
    <a class="btn btn-outline">Read More</a>
  </article>

  <p class="center copy" style="top:1797px;padding:0 180px">This website focuses on the governance layer and provides links to learn about structural concepts such as role separation, escrow and milestone framing, and recordkeeping terminology</p>
</section>

<section class="roles">
  <h2 class="abs" style="left:118px;top:1998px;font-size:31px">Clear Role Separation</h2>
  <div class="rule" style="left:118px;top:2065px"></div>
  <p class="abs copy justify" style="left:118px;top:2088px;width:430px">The ecosystem is designed around clear separation of responsibilities. Governance activities belong at the framework layer. Operational workflows, where available, belong on a separate operating platform designed for process execution and recordkeeping. Assets and project execution, where applicable, belong at the project level through ring-fenced structures created for specific initiatives. This separation is intended to reduce ambiguity and help stakeholders understand who is responsible for what.</p>
  <div class="photo photo-network" role="img" aria-label="Wooden blocks with person icons joined by lines on a pale blue surface"></div>
</section>

<section class="escrow">
  <div class="photo photo-stones" role="img" aria-label="Balanced stack of smooth stones with autumn foliage behind"></div>
  <h2 class="abs" style="left:649px;top:2531px;font-size:31px;line-height:47px;width:440px">Independent Escrow and Milestone Oversight</h2>
  <div class="rule" style="left:649px;top:2640px"></div>
  <p class="abs copy" style="left:649px;top:2664px;width:431px">Some initiatives use independent escrow arrangements to coordinate staged releases linked to milestone completion. Escrow can support execution discipline by requiring defined evidence before releases occur. Escrow does not guarantee outcomes, timelines, or success, and it is not administered by this website operator. This site describes the concept for clarity and transparency.</p>
</section>

<section class="band" style="top:3041px;height:419px"></section>
<section class="workflows">
  <h2 class="center" style="top:3108px;font-size:31px">Where Operational Workflows Happen</h2>
  <div class="rule" style="left:580px;top:3169px"></div>
  <p class="center copy" style="top:3205px;padding:0 195px">Operational workflows, including any onboarding or workflow participation where permitted, occur on a separate operating platform under separate terms and policies. If you need operational access, use the Halvemark page on this site to navigate externally. This website does not host those workflows.</p>
  <a class="btn btn-dark" style="left:483px;top:3348px;width:234px;height:45px">Learn the Framework</a>
</section>

<footer class="footer">
  <div class="brand" style="left:118px;top:98px;font-size:21px"><span class="brand-dot"></span>The Copper Lantern</div>
  <a class="btn btn-violet" style="left:118px;top:195px;width:196px;height:40px;font-size:13px">Continue to Halvemark</a>
  <p class="legal">© 2026 The Copper Lantern.<br>All rights reserved</p>

  <h4 style="left:458px">Quick Links</h4>
  <ul style="left:458px"><li>Framework</li><li>Projects</li><li>Halvemark</li><li>Insights</li><li>Company</li><li>Contact</li><li>Glossary</li></ul>

  <h4 style="left:688px">Company</h4>
  <ul style="left:688px"><li>About</li><li>Leadership</li><li>Governance</li><li>Press</li><li>Careers</li><li>Contact</li></ul>

  <h4 style="left:897px">Legal</h4>
  <ul style="left:897px"><li>Legal (Index)</li><li>Terms of Use</li><li>Privacy Policy</li><li>Cookie Policy</li><li>Disclaimer &amp; Risk Notices</li><li>Acceptable Use Policy</li><li>Accessibility Statement</li></ul>
</footer>

</body>
</html>
```